Splash Screen for a new release of software

Our company Tarnwick Asia Pacific writes business management software for the automotive industry. Early next year we are planning on releasing our new version of Velcorin, this is a fourth generation product. Our thoughts are to brand this version simply Velcorin 4, however we do wish to add a certain exclusivity to product hence the addition of Lantern Edition as a signature to the Velcorin brand. The splash screen has to make the user feel that they are using an upmarket product and are excited to be doing so. I have uploaded an "in house" design for reference purposes, also included our sphere company logo.

```html
<!DOCTYPE html>
<html lang="en">
<head>
<meta charset="utf-8">
<title>Velcorin 4 Lantern Edition – Splash Screens</title>
<link rel="stylesheet" href="https://fonts.googleapis.com/css2?family=Montserrat:wght@400;500&family=Tinos&display=swap">
<style>
  :root {
    --page: #ffffff;
    --ink: #ffffff;
    --night: #050306;
    --violet: #7a3a9a;
    --indigo: #1a1f5e;
    --plum: #3a0f3a;
    --magenta: #d0167a;
  }
  html, body {
    margin: 0;
    width: 1200px;
    height: 898px;
    overflow: hidden;
    background: var(--page);
  }
  .splash {
    position: absolute;
    left: 362px;
    width: 482px;
    height: 328px;
    overflow: hidden;
    color: var(--ink);
    font-family: "Montserrat", sans-serif;
  }
  .splash--inline { top: 90px; }
  .splash--numeral { top: 485px; }
  .splash__art {
    position: absolute;
    inset: 0;
    background:
      radial-gradient(ellipse 120px 70px at 210px 190px, rgba(122,58,154,.55), transparent 70%),
      radial-gradient(ellipse 140px 110px at 80px 250px, rgba(26,31,94,.7), transparent 70%),
      radial-gradient(ellipse 110px 120px at 340px 240px, rgba(122,58,154,.45), transparent 70%),
      radial-gradient(ellipse 90px 60px at 400px 270px, rgba(58,15,58,.8), transparent 70%),
      radial-gradient(ellipse 120px 60px at 240px 20px, rgba(26,31,94,.6), transparent 70%),
      radial-gradient(ellipse 70px 40px at 150px 40px, rgba(122,58,154,.35), transparent 70%),
      radial-gradient(ellipse 60px 30px at 430px 130px, rgba(122,58,154,.4), transparent 70%),
      radial-gradient(ellipse 130px 90px at 40px 170px, rgba(58,15,58,.55), transparent 70%),
      var(--night);
  }
  .splash__title {
    position: absolute;
    left: 9px;
    top: 4px;
    margin: 0;
    font-family: "Tinos", "Times New Roman", serif;
    font-weight: 400;
    font-size: 45px;
    line-height: 1;
    letter-spacing: .5px;
    text-transform: uppercase;
  }
  .splash__edition {
    position: absolute;
    left: 7px;
    top: 43px;
    margin: 0;
    font-size: 16px;
    font-weight: 400;
    letter-spacing: .3px;
  }
  .splash__numeral {
    position: absolute;
    left: 0;
    top: 0;
  }
  .splash__date {
    position: absolute;
    left: 8px;
    top: 312px;
    font-size: 9px;
  }
  .splash__credits {
    position: absolute;
    left: 141px;
    width: 200px;
    top: 300px;
    text-align: center;
    font-size: 9px;
    line-height: 11.5px;
  }
  .brand-mark {
    position: absolute;
    left: 396px;
    top: 243px;
    width: 66px;
    height: 66px;
    border-radius: 50%;
    background: radial-gradient(circle, var(--magenta) 0%, rgba(208,22,122,.55) 55%, transparent 72%);
    display: flex;
    align-items: center;
    justify-content: center;
  }
  .brand-mark__name {
    font-size: 8px;
    font-weight: 500;
    letter-spacing: .4px;
    text-transform: uppercase;
    color: var(--ink);
  }
</style>
</head>
<body>
  <section class="splash splash--inline">
    <div class="splash__art" role="img" aria-label="Abstract flowing ribbons in violet, indigo and plum on a near-black background"></div>
    <h1 class="splash__title">Velcorin 4</h1>
    <p class="splash__edition">Lantern Edition</p>
    <div class="brand-mark"><span class="brand-mark__name">Tarnwick</span></div>
    <span class="splash__date">January 21, 2025</span>
    <div class="splash__credits">Version 4.0.0<br>© Tarnwick Asia Pacific Pty Ltd 2016</div>
  </section>

  <section class="splash splash--numeral">
    <div class="splash__art" role="img" aria-label="Abstract flowing ribbons in violet, indigo and plum on a near-black background"></div>
    <h1 class="splash__title">Velcorin</h1>
    <p class="splash__edition">Lantern Edition</p>
    <svg class="splash__numeral" width="482" height="328" viewBox="0 0 482 328" aria-label="4">
      <path d="M247 121 L213 182 L271 182 M253 121 L253 208" fill="none" stroke="#ffffff" stroke-width="2.5"/>
    </svg>
    <div class="brand-mark"><span class="brand-mark__name">Tarnwick</span></div>
    <span class="splash__date">January 21, 2025</span>
    <div class="splash__credits">Version 4.0.0<br>© Tarnwick Asia Pacific Pty Ltd 2016</div>
  </section>
</body>
</html>
```